Keystone Trench Co Business Card*

Looking for a professional, clean and crisp business card

I am in the underground utilities industry and am just looking for a really impressive business card. I would like our card to be white with our symbol crisp and clear with it protruding. I also have a business partner that will require his name and info on the card once the design is set. I would like to have our website info on the card which is;
http://keystonetrenchco.example/

Contact Information for Business Card

Website, contact name, number and email

```html
<!DOCTYPE html>
<html lang="en">
<head>
<meta charset="utf-8">
<title>Keystone Trench Co — Business Card</title>
<link rel="stylesheet" href="https://fonts.googleapis.com/css2?family=Bebas+Neue&display=swap">
<style>
  :root {
    --backdrop: #b9bfc2;
    --card: #f3f3f1;
    --card-edge: #1d3a8a;
    --ink-blue: #3a62b0;
    --ink-red: #e0262b;
    --ink-grey: #5a5a5a;
    --ink-dark: #1c1c1c;
    --rule: #4a4a4a;
  }
  * { margin: 0; padding: 0; box-sizing: border-box; }
  html, body {
    width: 1200px;
    height: 824px;
    overflow: hidden;
    background: var(--backdrop);
  }
  .card {
    position: absolute;
    left: 100px;
    top: 126px;
    width: 1000px;
    height: 572px;
    background: var(--card);
    border-bottom: 4px solid var(--card-edge);
    border-left: 2px solid var(--card-edge);
    box-shadow: 0 10px 30px rgba(0,0,0,0.18);
    font-family: "Bebas Neue", sans-serif;
  }
  .brand {
    position: absolute;
    right: 70px;
    top: 60px;
    width: 300px;
    display: flex;
    align-items: center;
    justify-content: center;
    gap: 16px;
    height: 230px;
  }
  .brand-dot {
    width: 46px;
    height: 46px;
    border-radius: 50%;
    background: var(--ink-dark);
    flex: none;
  }
  .brand-name {
    font-size: 46px;
    line-height: 1;
    color: var(--ink-dark);
    letter-spacing: 1px;
  }
  .divider {
    position: absolute;
    left: 70px;
    right: 70px;
    top: 345px;
    height: 1.5px;
    background: var(--rule);
  }
  .person {
    position: absolute;
    left: 70px;
    top: 262px;
  }
  .person-name {
    font-size: 60px;
    line-height: 0.95;
    color: var(--ink-blue);
    letter-spacing: 1px;
  }
  .person-title {
    font-size: 28px;
    line-height: 1;
    color: var(--ink-red);
    letter-spacing: 0.5px;
  }
  .contact {
    position: absolute;
    left: 70px;
    top: 368px;
    list-style: none;
    font-size: 27px;
    line-height: 1.15;
    color: var(--ink-grey);
    letter-spacing: 0.5px;
  }
  .company-address {
    position: absolute;
    right: 70px;
    top: 362px;
    text-align: right;
    font-style: normal;
    font-size: 27px;
    line-height: 1.15;
    color: var(--ink-grey);
    letter-spacing: 0.5px;
  }
</style>
</head>
<body>
  <section class="card">
    <div class="brand">
      <span class="brand-dot"></span>
      <span class="brand-name">Keystone Trench Co</span>
    </div>

    <div class="person">
      <h1 class="person-name">Daniel Reyes</h1>
      <p class="person-title">President</p>
    </div>

    <div class="divider"></div>

    <ul class="contact">
      <li>555-214-7730</li>
      <li>info@keystonetrenchco.example</li>
      <li>www.keystonetrenchco.example</li>
    </ul>

    <address class="company-address">
      Keystone Trench Co LLC<br>
      4120 Alder Ridge Road<br>
      Anchorage, Alaska 99517
    </address>
  </section>
</body>
</html>
```